Candle Rental Business seeks new website design

We need a new website design for a Candle hire business. The business rents out pillar candles for events such as weddings and corporate events. Our main target market is weddings. The business name is Hire a Lantern. The business name does not have a logo design.

We would like a website that is light in colours and creates a warm atmosphere. The design needs to be elegant and upmarket. There are different size candles that we hire out, ranging from 10cm diameter to 20cm diameter, flat, tall etc. All our candles are white in colour. Its just the size that differs.

We would also like to include a section for hiring out decor such as glassvases, candlebras, overlays and chairs sachets, chair covers. However, this is not the businesses main focus but an additional offering to customers.

Target Market(s)

Wedding venues and brides. Corporate events. School dances.

Industry/Entity Type

Hospitality

Logo Text

Hire a Lantern

Number of Pages Required

1 page

Font styles to use
Sans Serif
Script

Requirements
Must have
• Pictures of pillar candles. Plain white candles. The website must centre around candles.
Nice to have
• Different examples of candle centrepieces
Should not have
• Pictures must not be of brides. Pictures of surrounding is perferable.

```html
<!DOCTYPE html>
<html lang="en">
<head>
<meta charset="utf-8">
<title>Hire a Lantern – Candle Hire</title>
<link href="https://fonts.googleapis.com/css2?family=Lato:wght@400;700&family=Questrial&family=Lobster&family=Arvo:wght@700&display=swap" rel="stylesheet">
<style>
:root{
  --orange:#f07c12;
  --amber:#f8b419;
  --purple:#9a6cc0;
  --ink:#222;
  --text:#555;
  --muted:#777;
  --cream:#f4f1e6;
  --grey:#ececec;
  --white:#fff;
  --green:#6f9a35;
  --dark:#2b2b2b;
  --blue:#3d80c8;
}
*{box-sizing:border-box;margin:0;padding:0}
html,body{width:1200px;height:2727px;overflow:hidden}
body{position:relative;background:var(--white);font-family:"Lato",sans-serif;color:var(--text)}
.abs{position:absolute}
h2,h3{font-family:"Questrial",sans-serif;font-weight:400;color:var(--ink)}

/* header */
.site-header{position:absolute;left:0;top:0;width:1200px;height:86px;background:var(--white)}
.brand{position:absolute;left:80px;top:12px;display:flex;align-items:center;gap:16px}
.brand-mark{width:26px;height:26px;background:var(--orange);border-radius:50%}
.brand-name{font-family:"Questrial",sans-serif;font-size:37px;color:var(--ink)}
.account-links{position:absolute;right:80px;top:11px;display:flex;gap:34px;font-size:14px;color:var(--text)}
.account-links span{display:flex;align-items:center;gap:8px}
.main-nav{position:absolute;right:80px;top:52px;display:flex;gap:38px;font-family:"Questrial",sans-serif;font-size:17px;color:var(--ink)}
.main-nav a{color:inherit;text-decoration:none;padding:3px 8px}
.main-nav a.active{color:var(--orange);border:1px solid var(--orange)}

/* hero */
.hero{position:absolute;left:0;top:86px;width:1200px;height:534px;
  background:radial-gradient(ellipse at 25% 20%,#7a4aa8 0%,#3a2440 30%,transparent 55%),
             radial-gradient(ellipse at 80% 60%,#d9c9cf 0%,#9e8a86 35%,transparent 70%),
             linear-gradient(180deg,#3b2a2a 0%,#7b6860 55%,#cfc4bf 100%)}
.hero-badge{position:absolute;left:410px;top:96px;width:380px;height:380px;border-radius:50%;
  background:rgba(255,255,255,.82);text-align:center;padding-top:70px}
.hero-title{font-family:"Lobster",cursive;font-size:50px;line-height:50px;color:var(--purple)}
.hero-sub{font-family:"Arvo",serif;font-size:23px;line-height:31px;color:#5a5047;margin-top:22px}
.hero-arrow{position:absolute;top:238px}

/* about */
.about{position:absolute;left:0;top:620px;width:1200px;height:282px;text-align:center}
.about h2{font-size:41px;margin-top:48px}
.about p{width:1040px;margin:20px auto 0;font-size:13.5px;line-height:26px;color:var(--text)}
.read-more{display:inline-block;margin-top:26px;font-size:16px;color:var(--orange);text-decoration:underline}

/* services */
.services{position:absolute;left:0;top:902px;width:1200px;height:623px;background:var(--cream)}
.card{position:absolute;background:var(--white)}
.card h3{font-size:26px}
.card p{font-size:13.5px;line-height:26px;color:var(--text)}
.btn{display:inline-block;background:var(--green);color:var(--white);font-size:12px;padding:7px 18px}
.photo{position:absolute}

/* how it works */
.how{position:absolute;left:0;top:1525px;width:1200px;height:475px;text-align:center}
.how h2{font-size:41px;margin-top:52px}
.step{position:absolute;top:178px;width:200px;text-align:center}
.step-icon{width:150px;height:150px;border-radius:50%;margin:0 auto;display:flex;align-items:center;justify-content:center}
.step-label{font-size:22px;line-height:29px;color:var(--muted);margin-top:22px}

/* decor */
.decor{position:absolute;left:0;top:2000px;width:1200px;height:385px;background:var(--grey);text-align:center}
.decor h2{font-size:41px;margin-top:52px}
.tile{position:absolute;top:153px;width:254px;height:188px;display:flex;align-items:center;justify-content:center}
.tile::after{content:"";position:absolute;inset:10px;border:2px solid rgba(255,255,255,.7)}
.tile span{position:relative;font-family:"Lato",sans-serif;font-weight:700;font-size:23px;line-height:30px;color:var(--white)}

/* footer */
.site-footer{position:absolute;left:0;top:2385px;width:1200px;height:295px;background:var(--cream)}
.footer-col{position:absolute;top:42px}
.footer-col h4{font-family:"Lato",sans-serif;font-weight:400;font-size:15px;color:var(--ink);padding-bottom:8px;border-bottom:1px solid #ddd8c7}
.quick-links li{list-style:none;font-size:12.5px;color:var(--text);margin-top:31px;padding-left:18px;position:relative}
.quick-links li::before{content:"";position:absolute;left:0;top:5px;width:5px;height:5px;border:1px solid var(--text);border-radius:50%}
.contact-row{display:flex;gap:16px;font-size:12.5px;line-height:19px;color:var(--text);margin-top:18px}
.field{width:240px;height:28px;border:1px solid #666;background:var(--white);font-size:11px;padding:4px 8px;margin-top:8px;color:var(--text)}
.submit{width:240px;height:32px;background:var(--orange);color:var(--white);font-size:14px;text-align:center;line-height:32px;margin-top:10px}
.social li{list-style:none;display:flex;align-items:center;gap:12px;font-size:12.5px;margin-top:12px}
.social i{display:block;width:32px;height:32px;border-radius:50%}
.copyright{position:absolute;left:0;top:2680px;width:1200px;height:47px;background:var(--dark);color:#ccc;font-size:14px}
.copyright .left{position:absolute;left:80px;top:15px}
.copyright .right{position:absolute;right:80px;top:11px;display:flex;align-items:center;gap:6px}
.card-name{display:inline-block;background:var(--white);color:var(--ink);font-size:10px;padding:5px 5px}
</style>
</head>
<body>

<header class="site-header">
  <div class="brand"><span class="brand-mark"></span><span class="brand-name">Hire a Lantern</span></div>
  <div class="account-links">
    <span><svg width="14" height="14" viewBox="0 0 14 14"><rect x="4" y="1" width="9" height="12" fill="none" stroke="#666"/><path d="M1 7h7M5 4l3 3-3 3" fill="none" stroke="#666"/></svg>log in</span>
    <span><svg width="14" height="14" viewBox="0 0 14 14"><rect x="1" y="1" width="12" height="12" fill="none" stroke="#666"/><path d="M4 5h6M4 8h6" stroke="#666"/></svg>Register</span>
  </div>
  <nav class="main-nav">
    <a class="active">Home</a><a>About Us</a><a>Our Products</a><a>Contact Us</a>
  </nav>
</header>

<section class="hero" role="img" aria-label="Photo of a candlelit table setting with floating candles in glass vases and purple orchids">
  <svg class="hero-arrow" style="left:26px" width="30" height="52" viewBox="0 0 30 52"><path d="M28 2L3 26l25 24" fill="none" stroke="#fff" stroke-width="2"/></svg>
  <svg class="hero-arrow" style="right:26px" width="30" height="52" viewBox="0 0 30 52"><path d="M2 2l25 24L2 50" fill="none" stroke="#fff" stroke-width="2"/></svg>
  <div class="hero-badge">
    <div class="hero-title">Decorative<br>Candles</div>
    <div class="hero-sub">Creating A Warm<br>Atmosphere &amp; Special<br>Touch To All<br>Occasions.</div>
  </div>
</section>

<section class="about">
  <h2>About Us</h2>
  <p>We are a family owned and operated company and began making decorative candles for all occasions.&nbsp; All of our candles are individually hand made in our candle studio, situated in Riverton, outside Harbourside.&nbsp; Our wax is local and of a very high quality, and dripless! Our wax is also made with a high melting point, which means it will not melt or bend in hot temperatures.</p>
  <a class="read-more">Read More</a>
</section>

<section class="services">
  <article class="card" style="left:96px;top:58px;width:382px;height:500px">
    <div class="photo" role="img" aria-label="Photo of white pillar candles on a glass centrepiece with blue stones" style="left:19px;top:18px;width:344px;height:236px;background:linear-gradient(160deg,#c9bca6 0%,#e8e4dc 45%,#7aa7b8 100%)"></div>
    <div style="position:absolute;left:19px;top:262px;width:350px">
      <h3>Hire Candles</h3>
      <p style="margin-top:8px">Do you love using candles for your events but tired of sorting old used candles or buying expensive the candles. Believe it or not you can now rent lorem is candles.All our candles come in different sizes and heights.You can add the ambience of.</p>
      <span class="btn" style="margin-top:14px">Read More</span>
    </div>
  </article>
  <article class="card" style="left:498px;top:58px;width:614px;height:240px">
    <div style="position:absolute;left:18px;top:12px;width:360px">
      <h3>Personalised Candles</h3>
      <p style="margin-top:6px">Hire a Lantern provides the opportunity to give a thoughtful, meaningful gift at a friendly price point. This unique gift conveys the time and care you put into creating it. The recipient will enjoy the beautiful presentation and be reminded of the sentiment...</p>
      <span class="btn" style="margin-top:8px">Read More</span>
    </div>
    <div class="photo" role="img" aria-label="Photo of two personalised candles in glass jars" style="left:393px;top:18px;width:202px;height:204px;background:linear-gradient(160deg,#ece8ea 0%,#dcd2d6 50%,#c5a0b4 100%)"></div>
  </article>
  <article class="card" style="left:498px;top:318px;width:614px;height:240px">
    <div style="position:absolute;left:18px;top:10px;width:360px">
      <h3>Décor Hire</h3>
      <p style="margin-top:6px">We hire a selection of overlays, chair sachets and chair covers as well as glassware and candelabras to compliment your décor.</p>
      <span class="btn" style="margin-top:14px">Read More</span>
    </div>
    <div class="photo" role="img" aria-label="Photo of a floral table centrepiece with candles and glassware" style="left:393px;top:18px;width:202px;height:204px;background:linear-gradient(160deg,#6b3a26 0%,#b27a4e 45%,#8fa45a 100%)"></div>
  </article>
</section>

<section class="how">
  <h2>How It Works</h2>
  <svg class="abs" style="left:245px;top:160px" width="120" height="40" viewBox="0 0 120 40"><path d="M2 30Q50 0 110 18M100 8l10 10-13 4" fill="none" stroke="#ccc" stroke-width="3"/></svg>
  <svg class="abs" style="left:545px;top:290px" width="120" height="40" viewBox="0 0 120 40"><path d="M2 20Q60 35 110 12M98 8l12 4-6 11" fill="none" stroke="#ccc" stroke-width="3"/></svg>
  <svg class="abs" style="left:845px;top:155px" width="120" height="40" viewBox="0 0 120 40"><path d="M2 30Q50 0 110 18M100 8l10 10-13 4" fill="none" stroke="#ccc" stroke-width="3"/></svg>

  <div class="step" style="left:54px">
    <div class="step-icon" style="background:var(--orange)">
      <svg width="70" height="90" viewBox="0 0 70 90"><path d="M35 4c6 8 8 14 0 22-8-8-6-14 0-22z" fill="#fff"/><rect x="18" y="32" width="34" height="52" rx="4" fill="#fff"/><path d="M18 48h34M18 64h34" stroke="var(--orange)" stroke-width="3"/></svg>
    </div>
    <div class="step-label">Choose your<br>Candle</div>
  </div>
  <div class="step" style="left:350px">
    <div class="step-icon" style="background:var(--amber)">
      <svg width="70" height="90" viewBox="0 0 70 90"><path d="M22 10a6 6 0 0 1 12 0v30h4a6 6 0 0 1 12 2v4a6 6 0 0 1 10 3v22c0 10-8 16-18 16H34c-8 0-12-4-16-10L6 56a6 6 0 0 1 10-6l6 8z" fill="#fff"/></svg>
    </div>
    <div class="step-label">Book your<br>Candle</div>
  </div>
  <div class="step" style="left:650px">
    <div class="step-icon" style="background:var(--orange)">
      <svg width="80" height="70" viewBox="0 0 80 70"><rect x="6" y="16" width="66" height="40" rx="3" fill="#fff" transform="rotate(-10 40 36)"/><circle cx="40" cy="36" r="11" fill="var(--orange)"/><circle cx="18" cy="38" r="4" fill="var(--orange)"/><circle cx="62" cy="32" r="4" fill="var(--orange)"/></svg>
    </div>
    <div class="step-label">Make<br>payment</div>
  </div>
  <div class="step" style="left:945px;top:170px">
    <div class="step-icon" style="background:var(--amber)">
      <svg width="80" height="96" viewBox="0 0 80 96"><path d="M40 4c5 7 6 12 0 18-6-6-5-11 0-18z" fill="#fff"/><rect x="28" y="28" width="24" height="40" fill="#fff"/><path d="M10 72h60l-8 8H18z" fill="#fff"/><rect x="34" y="80" width="12" height="8" fill="#fff"/><path d="M22 88h36" stroke="#fff" stroke-width="4"/></svg>
    </div>
    <div class="step-label">Light Up<br>Your Event</div>
  </div>
</section>

<section class="decor">
  <h2>Our Hiring Out Decor</h2>
  <div class="tile" role="img" aria-label="Photo of glass vases with candles" style="left:80px;background:linear-gradient(160deg,#3a3330 0%,#8b7d6e 50%,#2a2624 100%)"><span>Glass Vases</span></div>
  <div class="tile" role="img" aria-label="Photo of glass candelabras" style="left:342px;background:linear-gradient(160deg,#6e5f44 0%,#a8987a 50%,#5c4f3a 100%)"><span>Candle Bras</span></div>
  <div class="tile" role="img" aria-label="Photo of lace overlays and chair sashes" style="left:604px;background:linear-gradient(160deg,#3b3a38 0%,#8a8784 50%,#2c2b2a 100%)"><span>Overlays &amp;<br>Chairs Sachets</span></div>
  <div class="tile" role="img" aria-label="Photo of chair covers with pink sashes" style="left:866px;background:linear-gradient(160deg,#4a3e42 0%,#c3a2ac 50%,#4e4246 100%)"><span>Chair Covers</span></div>
</section>

<footer class="site-footer">
  <div class="footer-col" style="left:80px;width:110px">
    <h4>Quick Links</h4>
    <ul class="quick-links"><li style="margin-top:20px">Home</li><li>About Us</li><li>Our Products</li><li>Contact Us</li></ul>
  </div>
  <div class="footer-col" style="left:303px;width:215px">
    <h4>Contact Details</h4>
    <div class="contact-row" style="margin-top:14px"><svg width="18" height="22" viewBox="0 0 18 22"><path d="M9 1a7 7 0 0 0-7 7c0 5 7 13 7 13s7-8 7-13a7 7 0 0 0-7-7z" fill="none" stroke="#777" stroke-width="1.5"/><circle cx="9" cy="8" r="2.5" fill="none" stroke="#777"/></svg><span>1/23 Lorem Ips Dolo, Consecer<br>wererr Nonuy - 12345</span></div>
    <div class="contact-row" style="margin-top:22px"><svg width="18" height="22" viewBox="0 0 18 22"><path d="M4 2l4 1 1 5-3 2c1 3 3 5 6 6l2-3 5 1v4c-9 1-17-7-16-16z" fill="none" stroke="#777" stroke-width="1.5"/></svg><span style="font-size:14px">123-456-7890</span></div>
    <div class="contact-row" style="margin-top:30px"><svg width="18" height="14" viewBox="0 0 18 14"><rect x="1" y="1" width="16" height="12" fill="none" stroke="#777" stroke-width="1.5"/><path d="M1 1l8 7 8-7" fill="none" stroke="#777" stroke-width="1.5"/></svg><span style="font-size:14px">info@hirealantern.com</span></div>
  </div>
  <div class="footer-col" style="left:651px;width:240px">
    <h4>Quick Inquiry</h4>
    <div class="field">Name</div>
    <div class="field">Phone</div>
    <div class="field" style="height:48px">Message</div>
    <div class="submit">Submit</div>
  </div>
  <div class="footer-col" style="left:1002px;width:118px">
    <h4>Follow Us</h4>
    <ul class="social">
      <li style="color:var(--blue)"><i style="background:#3b5998"></i>Friendly</li>
      <li style="color:#55acee"><i style="background:#55acee"></i>Chirper</li>
      <li style="color:var(--blue)"><i style="background:#2f7ab7"></i>Linkup</li>
      <li style="color:#c9463d"><i style="background:#c9463d"></i>Circles</li>
    </ul>
  </div>
</footer>

<div class="copyright">
  <span class="left">Copyright © 2016 Hire a Lantern. All Rights Reserved.</span>
  <span class="right">We Accept:&nbsp;&nbsp;<span class="card-name">Nova</span><span class="card-name">Orbit</span><span class="card-name">Crest</span><span class="card-name">Tally</span></span>
</div>

</body>
</html>
```